Redesign of business card for Cedar Ridge Mechanical

We are looking for a new design for our business cards for Cedar Ridge Mechanical. We are a plumbing & HVAC construction company, operating on the West Coast of Canada and USA. Logo attached.
Industry/Entity Type
Construction - Plumbing & HVAC
Contact Information for Business Card
Name, address, phone numbers, email, website address
Look and feel
Each slider illustrates characteristics of the customer's brand and the style your logo design should communicate.

```html
<!DOCTYPE html>
<html lang="en">
<head>
<meta charset="utf-8">
<title>Cedar Ridge Mechanical – Business Card</title>
<link href="https://fonts.googleapis.com/css2?family=Poppins:wght@300;400;600&display=swap" rel="stylesheet">
<style>
  :root {
    --backdrop: #242425;
    --card: #1d1d1f;
    --card-edge: #3a3a3c;
    --ink-white: #ffffff;
    --ink-soft: #e6e6e6;
    --ink-emboss: #111112;
  }
  * { margin: 0; padding: 0; box-sizing: border-box; }
  html, body {
    width: 1200px; height: 711px; overflow: hidden;
    background: var(--backdrop);
    font-family: "Poppins", sans-serif;
  }
  .canvas { position: relative; width: 1200px; height: 711px; }
  .card {
    position: absolute; top: 207px;
    width: 520px; height: 297px;
    background: var(--card);
    border: 1px solid var(--card-edge);
    border-radius: 22px;
    box-shadow: 0 14px 30px rgba(0,0,0,.55);
    overflow: hidden;
  }
  .card-front { left: 50px; }
  .card-back { left: 630px; }

  .front-wordmark {
    position: absolute; inset: 0;
    display: flex; align-items: center; justify-content: center; gap: 12px;
    color: var(--ink-emboss);
    font-weight: 600; font-size: 26px; letter-spacing: .5px;
  }
  .front-wordmark .mark-square {
    width: 22px; height: 22px; background: var(--ink-emboss);
  }

  .back-wordmark {
    position: absolute; top: 48px; right: 30px;
    display: flex; align-items: center; gap: 10px;
    color: var(--ink-white);
    font-weight: 600; font-size: 19px;
  }
  .back-wordmark .mark-square {
    width: 18px; height: 18px; border: 2px solid var(--ink-white);
  }

  .divider {
    position: absolute; left: 262px; right: 0; top: 118px;
    height: 1.5px; background: var(--ink-white);
  }

  .person { position: absolute; left: 28px; top: 86px; color: var(--ink-white); }
  .person-name { font-size: 29px; line-height: 1.1; }
  .person-name .first { font-weight: 600; }
  .person-name .last { font-weight: 300; }
  .person-title { font-size: 14px; font-weight: 400; margin-top: 2px; color: var(--ink-soft); }

  .address {
    position: absolute; right: 30px; top: 132px;
    text-align: right; color: var(--ink-soft);
    font-size: 13px; font-weight: 300; line-height: 1.45;
  }
  .contact {
    position: absolute; right: 30px; top: 188px;
    list-style: none; color: var(--ink-soft);
    font-size: 13px; font-weight: 300;
  }
  .contact li {
    display: flex; justify-content: flex-end; align-items: center;
    gap: 8px; line-height: 1.7;
  }
  .contact svg { width: 12px; height: 12px; fill: none; stroke: var(--ink-white); stroke-width: 1.6; }
</style>
</head>
<body>
<main class="canvas">

  <section class="card card-front" aria-label="Card front">
    <div class="front-wordmark">
      <span class="mark-square"></span>
      <span>Cedar Ridge Mechanical</span>
    </div>
  </section>

  <section class="card card-back" aria-label="Card back">
    <div class="back-wordmark">
      <span class="mark-square"></span>
      <span>Cedar Ridge Mechanical</span>
    </div>

    <div class="divider"></div>

    <div class="person">
      <p class="person-name"><span class="first">Maren</span> <span class="last">Solvik</span></p>
      <p class="person-title">Founder &amp; CEO</p>
    </div>

    <p class="address">1840 Harbor Ln. Suite 310<br>Bellingham, WA 98225</p>

    <ul class="contact">
      <li>(360) 555-0147
        <svg viewBox="0 0 24 24"><path d="M5 3h4l2 5-3 2a12 12 0 0 0 6 6l2-3 5 2v4a2 2 0 0 1-2 2A18 18 0 0 1 3 5a2 2 0 0 1 2-2z"/></svg>
      </li>
      <li>info@yourwebsite.com
        <svg viewBox="0 0 24 24"><rect x="3" y="5" width="18" height="14" rx="1"/><path d="M3 6l9 7 9-7"/></svg>
      </li>
      <li>www.yourwebsite.com
        <svg viewBox="0 0 24 24"><circle cx="12" cy="12" r="9"/><path d="M3 12h18M12 3c3 3 3 15 0 18M12 3c-3 3-3 15 0 18"/></svg>
      </li>
    </ul>
  </section>

</main>
</body>
</html>
```